PowerPoint Listing Presentation for Real Estate Agency

We need a PowerPoint presentation for a new real estate brokerage team.

[[[[[[submit 1-3 sample slides for review - i will provide feedback and you can make changes if you want to - we will not be deciding on a design prior to the deadline]]]]]

******ATTN: DESIGNERS, if your skills are webdesign then just look at this like a portable website or a brochure. it should be easy enough******

NOTE: we have all the data to put into the slides. You just need to come up with the design and layout. we have a sample design that we like and have provided.

This focus will be for the home listing side of the business (a presentation for home sellers to convince them to use our services). The data and slides will present our team and the benefits, in the best light, to use our services over that of other real estate agent applying for the job. This presentation will proved facts and benefits and describe our special and unique offerings that will show a home seller why we can sell their home for more money in less time and with the least amount of hassle. The main color scheme is Dark Blue and White (we want some additional colors included - based on your creativity. otherwise the presentation will too monotone). We would like to see the use of Statistical Graphs (3-D) - data provided. We have photos of our team and a new logo (the logo could have some minor adjustment to clean it up if necessary) - also uploaded. We have about 80-90% of the information that will be put into the slides and will need to work closely to get the design and data integrated into the presentation (should be easier then it sounds). We should be able to add slides and data 'at will' over time via our master slides built into the presentation. We have a pretty good sample presentation that we like and can be used as a guideline (this is from our affiliated business network and we have full rights to all the information), it is uploaded but doesn't contain all the slide because of size limitations.

NOTE: An additional buyers presentation will be needed after we get the sellers presentation completed, which means additional work.

This should be enough to get you started and we are available if you have any questions to help you with the project. there will be around 60-70 total slides. once concept is completed it will be easy to create the slides.

Target Market(s)

home sellers. people who are moving to a new and better home or relocation for job reasons. typically more established in life

Industry/Entity Type

Real Estate

Requirements
Must have
• all the slides must be congruent. in other words, the exact same layout feel should used across the board. we are working on building our trade dress/image. Also, it must have a soft and inviting overall feel, yet show strength of ability.
Nice to have
• nice to have use of real people images when necessary. 3D graphs would be nice. clean modern look and feel, yet sophisticated and professional.
Should not have
• should not have a lot of time consuming transitions. do not include 3D stick figures or distracting moving gifs

```html
<!DOCTYPE html>
<html lang="en">
<head>
<meta charset="utf-8">
<title>Helping You Home – Harlow &amp; Pine Team</title>
<link rel="stylesheet" href="https://fonts.googleapis.com/css2?family=Gelasio:wght@400&family=Tinos:wght@400;700&display=swap">
<style>
  :root {
    --navy: #0c2f7a;
    --royal: #1454b8;
    --sky: #3f8fe0;
    --heading-blue: #1c4f8f;
    --ink: #3a3a3a;
    --paper: #f3f3f3;
    --paper-light: #fafafa;
    --logo-ink: #1b2350;
    --house-tone: #e4e4e4;
    --photo-dark: #2a2a2a;
    --photo-mid: #5d5a58;
  }
  * { margin: 0; padding: 0; box-sizing: border-box; }
  html, body { width: 1200px; height: 900px; overflow: hidden; }
  body { background: var(--paper); }

  .slide {
    position: relative;
    width: 1200px;
    height: 900px;
    overflow: hidden;
    background: radial-gradient(ellipse at 60% 50%, var(--paper-light) 0%, var(--paper) 70%);
  }
  .slide-waves { position: absolute; inset: 0; width: 1200px; height: 900px; }

  .house-motif {
    position: absolute;
    left: 420px; top: 120px;
    width: 780px; height: 560px;
    background: radial-gradient(ellipse at 50% 55%, var(--house-tone) 0%, rgba(228,228,228,0) 70%);
    opacity: .7;
  }

  .team-photo {
    position: absolute;
    left: 38px; top: 225px;
    width: 350px; height: 662px;
    border-radius: 60px 60px 10px 10px;
    background: linear-gradient(180deg, var(--photo-mid) 0%, var(--photo-dark) 35%, #1a1a1a 100%);
  }

  .brand-box {
    position: absolute;
    left: 762px; top: 27px;
    width: 396px; height: 110px;
    background: #fff;
    border: 2px solid var(--logo-ink);
    display: flex; align-items: center; justify-content: center; gap: 18px;
  }
  .brand-mark { width: 44px; height: 44px; background: var(--logo-ink); }
  .brand-name {
    font-family: "Tinos", "Times New Roman", serif;
    font-weight: 700;
    font-size: 31px;
    color: var(--logo-ink);
    letter-spacing: .5px;
  }

  .intro { position: absolute; left: 714px; top: 360px; width: 450px; }
  .intro-title {
    font-family: "Tinos", "Times New Roman", serif;
    font-weight: 400;
    font-size: 52px;
    line-height: 1.1;
    color: var(--heading-blue);
    margin-bottom: 26px;
    white-space: nowrap;
  }
  .intro-text {
    font-family: "Gelasio", Georgia, serif;
    font-size: 22.5px;
    line-height: 36px;
    color: var(--ink);
  }
</style>
</head>
<body>
<main class="slide">
  <div class="house-motif" role="img" aria-label="Faint outline of a house in the background"></div>

  <svg class="slide-waves" viewBox="0 0 1200 900" aria-hidden="true">
    <defs>
      <linearGradient id="topBand" x1="0" y1="0" x2="1" y2="1">
        <stop offset="0" stop-color="#0a3a94"/>
        <stop offset=".5" stop-color="#1560c4"/>
        <stop offset="1" stop-color="#0b3d9a"/>
      </linearGradient>
      <linearGradient id="bottomBand" x1="0" y1="0" x2="0" y2="1">
        <stop offset="0" stop-color="#13489e"/>
        <stop offset="1" stop-color="#0a2a78"/>
      </linearGradient>
    </defs>
    <!-- top band -->
    <path d="M0 0 H1200 V40 C1000 30 820 70 640 120 C440 175 220 200 0 195 Z" fill="url(#topBand)"/>
    <path d="M0 180 C220 188 440 165 640 118 C800 80 980 40 1200 38 V52 C980 56 810 96 650 140 C450 190 220 212 0 208 Z" fill="#ffffff"/>
    <path d="M0 205 C220 210 450 188 650 138 C810 98 980 58 1200 52 V58 C980 64 815 104 655 146 C455 196 220 218 0 214 Z" fill="var(--sky)"/>
    <!-- bottom band -->
    <path d="M0 775 C260 758 520 778 760 812 C940 838 1080 860 1200 870 V900 H0 Z" fill="var(--sky)"/>
    <path d="M0 790 C260 775 520 792 760 826 C940 850 1080 870 1200 878 V900 H0 Z" fill="#ffffff"/>
    <path d="M0 800 C260 788 520 805 760 838 C940 862 1080 880 1200 886 V900 H0 Z" fill="url(#bottomBand)"/>
  </svg>

  <div class="team-photo" role="img" aria-label="Photo of the two team members standing side by side in dark suits"></div>

  <div class="brand-box">
    <span class="brand-mark"></span>
    <span class="brand-name">HARLOW &amp; PINE TEAM</span>
  </div>

  <section class="intro">
    <h1 class="intro-title">Helping You Home</h1>
    <p class="intro-text">Lorem ipsum dolor sit Lorem ipsum dolor sit Lorem ipsum dolor sit Lorem ipsum dolor sit</p>
  </section>
</main>
</body>
</html>
```